Electrician Letterhead Design MVR

We need some letterhead for our bills and other papers.
Customer address is on the right side (Swiss format)
A4 format

Design should also be applicable on Cards

Target Market(s)

Private Customers, Small Business

Industry/Entity Type

Electrician

Other font styles liked:
• incised 901

Colors
00AB8E
00BBA5
67D7C9
C6EFE9
E9F9F6

```html
<!DOCTYPE html>
<html lang="en">
<head>
<meta charset="utf-8">
<title>MVR Letterhead</title>
<link href="https://fonts.googleapis.com/css2?family=Arimo:wght@400;700&display=swap" rel="stylesheet">
<style>
  :root{
    --teal:#00a08a;
    --ink:#555a5e;
    --dark:#1a1a1a;
    --backdrop:#e4e4e4;
    --paper:#ffffff;
  }
  *{margin:0;padding:0;box-sizing:border-box;}
  html,body{width:1189px;height:1200px;overflow:hidden;background:var(--backdrop);}
  body{font-family:"Arimo",Arial,sans-serif;color:var(--ink);}
  .sheet{position:absolute;left:184px;top:20px;width:820px;height:1160px;background:var(--paper);box-shadow:0 2px 8px rgba(0,0,0,.18);}
  .brand{position:absolute;left:0;right:0;top:52px;text-align:center;}
  .brand-name{display:block;font-weight:700;font-size:62px;line-height:62px;color:var(--teal);letter-spacing:2px;}
  .brand-full{display:block;margin-top:8px;font-weight:700;font-size:10px;letter-spacing:.6px;color:var(--dark);}
  .salutation{position:absolute;left:74px;top:356px;font-size:18px;font-weight:700;color:var(--ink);}
  .body-copy{position:absolute;left:73px;top:410px;width:672px;font-size:13.4px;line-height:16.8px;}
  .body-copy p{margin-bottom:15px;}
  .closing{position:absolute;left:74px;top:758px;font-size:10px;font-weight:700;}
  .signature{position:absolute;left:74px;top:806px;width:134px;height:42px;background:linear-gradient(90deg,#f1f1f1,#e6e6e6);border-radius:4px;}
  .footer-rule{position:absolute;left:0;top:1097px;width:820px;height:24px;}
  .contact{position:absolute;left:0;right:0;top:1124px;text-align:center;font-size:12.6px;white-space:nowrap;}
  .contact span{margin:0 5px;}
  .contact svg{vertical-align:-1px;margin-right:6px;}
</style>
</head>
<body>
  <main class="sheet">
    <header class="brand">
      <span class="brand-name">MVR</span>
      <span class="brand-full">Elektrotechnik Vollmer Rhein GmbH</span>
    </header>

    <h1 class="salutation">Dear Mr. Berger,</h1>

    <section class="body-copy">
      <p>Lorem ipsum dolor sit amet, consectetuer adipiscing elit, sed diam nonmmy nibh euismod tincidunt ut laor eet dolore magna aliquam erat volutpat. Ut wisi enim ad minim veniam, quis nostrud exerci tationmcorper suscipit lobortis nisl ut aliquip ex ea commodo consequat. Duis autem vel eum iriure dolor in hendrerit in vulputate velit esse molestie consequat, vel illum dolore eu feugiat</p>
      <p>Rorem ipsum dolor sit amet, consectetuer adipiscing elit, sed diam nonmmy nibh euismod tincidunt ut laor eet dolore magna aliquam erat volutpat. Ut wisi enim ad minim veniam, quis nostrud exerci tationmcorper suscipit lobortis nisl ut aliquip ex ea commodo consequat. Duis autem vel eum iriure dolor in hendrerit in vulputate velit esse molest</p>
      <p>Dorem ipsum dolor sit amet, consectetuer adipiscing elit, sed diam nonmmy nibh euismod tincidunt ut laor eet dolore magna aliquam erat volutpat. Ut wisi enim ad minim veniam, quis nostrud exerci tationmcorper suscipit lobortis nisl ut aliquip ex ea commodo consequat. Duis autem vel eum iriure dolor in hendrerit in suscipit lobortis nisl ut aliquip ex ea commodo consequat. Duis autem vel eum iriure dolor in hendrerit in vulputate velit esse molestie consequat, vel illum</p>
      <p>Sorem ipsum dolor sit amet, consectetuer adipiscing elit, sed diam nonmmy nibh euismod tincidunt ut laor eet dolore magna aliquam erat volutpat. Ut wisi enim ad minim veniam, quis nostrud exerci tationmcorper suscipit lobortis nisl ut aliquip ex ea commodo consequat. Duis autem vel eum iriure dolor in</p>
    </section>

    <p class="closing">Sincerely,</p>
    <div class="signature" role="img" aria-label="Handwritten signature of the sender"></div>

    <svg class="footer-rule" viewBox="0 0 820 24" aria-hidden="true">
      <rect x="0" y="9" width="768" height="6" fill="var(--teal)"/>
      <polyline points="752,1 763,12 752,23" fill="none" stroke="var(--teal)" stroke-width="6" stroke-linejoin="miter"/>
      <rect x="774" y="9" width="46" height="6" fill="var(--dark)"/>
    </svg>

    <footer class="contact">
      <span><svg width="10" height="10" viewBox="0 0 10 10"><path d="M2 0.5 L4 2.8 L3 4 Q4.5 6 6 7 L7.2 6 L9.5 8 L8 9.5 Q3.5 9 0.5 2 Z" fill="var(--teal)"/></svg>123-456-2100</span>
      <span><svg width="11" height="8" viewBox="0 0 11 8"><rect width="11" height="8" fill="var(--teal)"/><polyline points="0,0 5.5,4.5 11,0" fill="none" stroke="#fff" stroke-width="1"/></svg>office@mvr-elektro.ch</span>
      <span><svg width="10" height="10" viewBox="0 0 10 10"><circle cx="5" cy="5" r="5" fill="var(--teal)"/><ellipse cx="5" cy="5" rx="2" ry="4.4" fill="none" stroke="#fff" stroke-width=".8"/><line x1="0.6" y1="5" x2="9.4" y2="5" stroke="#fff" stroke-width=".8"/></svg>www.mvr-elektro.ch</span>|<span>Your address, city, state, ZIP 0000</span>
    </footer>
  </main>
</body>
</html>
```